New Website Announcement

We need a flyer to announce our new website to customers and prospective clients. The website will be launching soon, but I can provide a detailed outline in PDF form with copy and imagery to serve as inspiration for this design.

I would like a postcard size document that can be mailed in an envelope (no need for postcard style mailer info on 1 side)

About my company:

Verity Lane Studio is a new breed of marketing consulting agency built for the next frontier of consumer learning. Social interaction will be at the heart of great insights going forward – in how consumers engage with brands and in how organizations socialize what they learn to gain competitive advantage.
By fusing innovative insights techniques, technology and compelling graphic design-based reporting, we ensure results get noticed and make an impact.

contact info that can also be included:

Email: marek@veritylane-studio.net

Phone: 518-732-5164

Thanks

Attention all designers submitting a design for this project. Please keep in mind a few important details about this project.

1. Remember that the main objective of this postcard is to announce my new website.

2. Please be sure to read the brief for the copy I would like on each side. You can be creative in how it is displayed, but I need this key information somewhere. All other copy on the attached files is for your background only.

3. Please do not submit overly simple designs that just take the images I provided and overlay a text box with my copy. I could easily do this myself in PowerPoint in 5 minutes.

4. Remember that the design should be edgy and modern but needs to be professional and speak to a business audience.

Please submit any questions. Thank you for your submissions. 

Marek

Target Market(s)

senior level marketing and research clients at large companies and agencies

Industry/Entity Type

Marketing

Requirements
Must have
• Main message:

Need an engaging way to tell customers and prospective clients that we have a new website and that they should come visit us online to learn more about out services, check out case studies and read about our exciting partnerships.

COPY TO USE - UPDATED

Side 1:
(logo)
Introducing Verity Lane Studio

Let’s talk about taking research out of the dark ages.

Visit our newly launched website to learn how and get in touch.

www.veritylane-studio.net

Side 2
Logo
followed by tagline:
Consumer insights that get noticed.
A leading-edge marketing partnership that really works.

Additional text to use on Side 2:
How we can help...

Think of us as your go-to resource for identifying and incorporating the most innovative and exciting techniques into your research programs. We carefully curate and develop close partnerships with the best of the best - from online qualitative research and mobile ethnography to social media listening and fresh takes on concept testing, we can guide the way.

Plus, we believe that socializing consumer learning is just as critical as gathering it.By taking insights deliverables to the next level – through infographics, videos, magazines,interactive profiles and so much more – we are getting stakeholders excited to engage with research and inspired to take action because of it.
It’s a new way to look at insights from a new type of partner. And, it’s a new way to get the most from your research dollars.
Nice to have
• could incorporate our website main image of the lamp on white brick background which is attached, but not 100% mandatory.
Should not have
• - should not be too playful or young, but needs to be modern and design focused

- should not be cluttered or overly 'salesy'

- needs to be upscale and elegant / compelling and aligned with the look and feel of the website imagery (see attached)

```html
<!DOCTYPE html>
<html lang="en">
<head>
<meta charset="utf-8">
<title>Verity Lane Studio – New Website Postcard</title>
<link rel="stylesheet" href="https://fonts.googleapis.com/css2?family=Oswald:wght@300;400;500&family=Roboto+Condensed:wght@400;700&family=Arimo:ital,wght@0,400;0,700;1,700&family=Open+Sans:wght@700&display=swap">
<style>
  :root{
    --page:#e6e3de;
    --ink:#1e1e1e;
    --ink-soft:#3a3a3a;
    --brand:#1f6fb4;
    --brand-dark:#0d4a8c;
    --band-a:#0c4f96;
    --band-b:#2f86d2;
    --violet:#33339a;
    --sky:#8fc3ea;
    --sky-deep:#6aa9db;
    --brick:#dcdcdc;
    --brick-light:#f4f4f4;
    --panel:rgba(40,44,52,.86);
    --white:#ffffff;
    --tab:#f2f2f2;
    --tab-line:#b9b9b9;
    --cta-grey:#5c6672;
  }
  *{box-sizing:border-box;margin:0;padding:0}
  html,body{width:1200px;height:518px;overflow:hidden}
  body{background:var(--page);position:relative;font-family:"Arimo",Arial,sans-serif;color:var(--ink)}

  .postcard{position:absolute;height:428px;overflow:hidden;box-shadow:0 2px 6px rgba(0,0,0,.25)}
  .postcard--front{left:30px;top:30px;width:553px}
  .postcard--back{left:616px;top:59px;width:554px}

  .scene-photo{position:absolute;inset:0;
    background:radial-gradient(ellipse 260px 200px at 190px 140px,var(--brick-light),var(--brick) 70%,#bdbdbd)}
  .scene-wall{position:absolute;inset:0;
    background:linear-gradient(180deg,var(--sky) 0%,#a9d2f0 45%,var(--sky-deep) 100%)}

  .contact{position:absolute;left:30px;top:25px}
  .contact__phone{display:flex;align-items:center;gap:4px;font-family:"Arimo",Arial,sans-serif;font-size:16px;font-weight:700;color:var(--ink)}
  .contact__email{display:flex;align-items:center;gap:5px;font-size:12px;color:var(--ink-soft);margin-top:4px}

  .wordmark{position:absolute;right:28px;top:28px;text-align:right;font-family:"Oswald",Arial,sans-serif;font-weight:500;font-size:24px;color:var(--brand);text-transform:uppercase;line-height:1.05}
  .wordmark span{display:block}

  .site-nav{position:absolute;left:246px;display:flex;gap:4px}
  .postcard--front .site-nav{top:98px}
  .postcard--back .site-nav{top:96px}
  .site-nav__tab{width:43px;text-align:center;background:var(--tab);border:1px solid var(--tab-line);font-family:"Roboto Condensed",Arial,sans-serif;font-size:9.5px;color:var(--ink-soft);height:17px;line-height:15px;box-shadow:0 1px 2px rgba(0,0,0,.18);white-space:nowrap}
  .site-nav__tab--active{color:var(--brand);font-size:12px;height:19px;line-height:17px;margin-top:-2px}

  .headline{position:absolute;left:94px;top:164px;width:200px;text-align:center;font-family:"Oswald",Arial,sans-serif;font-weight:300;font-size:20px;line-height:26px;color:var(--ink-soft);text-transform:uppercase}
  .invite{position:absolute;left:0;right:0;top:360px;text-align:center;font-family:"Roboto Condensed",Arial,sans-serif;font-weight:700;font-size:17px;color:var(--ink)}

  .url-band{position:absolute;left:0;right:0;top:390px;height:26px;display:flex;align-items:center;justify-content:center;
    background:linear-gradient(90deg,var(--band-a),var(--band-b) 50%,var(--band-a));color:var(--white);font-family:"Arimo",Arial,sans-serif;font-size:16px}
  .url-band__icon{position:absolute;left:28px;top:5px}
  .social{position:absolute;right:30px;top:4px;display:flex;gap:4px}
  .social__dot{width:18px;height:18px;border:1.5px solid var(--white);border-radius:3px;background:#1a1a1a}

  .tagline{position:absolute;left:222px;top:27px;width:166px;text-align:center;font-family:"Open Sans",Arial,sans-serif;font-weight:700;font-size:14.5px;line-height:20px;color:var(--ink)}
  .strapline{position:absolute;left:30px;top:70px;font-family:"Arimo",Arial,sans-serif;font-style:italic;font-weight:700;font-size:14.5px;line-height:20px;color:var(--violet)}

  .feature{position:absolute;top:122px;width:135px}
  .feature__card{height:85px;background:rgba(255,255,255,.55);box-shadow:0 1px 4px rgba(0,0,0,.2);text-align:center;font-family:"Roboto Condensed",Arial,sans-serif;font-size:12px;color:var(--ink);padding-top:11px}
  .feature__mark{display:block;margin:8px auto 0;width:38px;height:38px}
  .feature__cta{margin-top:4px;height:20px;line-height:20px;text-align:center;color:var(--white);font-family:"Roboto Condensed",Arial,sans-serif;font-size:12px;background:linear-gradient(180deg,#3f8ad4,var(--brand-dark))}
  .feature__cta--grey{background:linear-gradient(180deg,#7a848f,var(--cta-grey))}
  .feature__cta::after{content:"";display:inline-block;margin-left:3px;border-left:6px solid #f6b21a;border-top:5px solid transparent;border-bottom:5px solid transparent}

  .help-panel{position:absolute;left:29px;top:238px;width:497px;height:144px;background:var(--panel);color:var(--white);padding:14px 24px 0 29px}
  .help-panel__title{font-family:"Arimo",Arial,sans-serif;font-weight:400;font-size:13.5px;margin-bottom:7px}
  .help-panel p{font-size:7.6px;line-height:10.2px;margin-bottom:8px}
</style>
</head>
<body>

<section class="postcard postcard--front" aria-label="Front side">
  <div class="scene-photo" role="img" aria-label="Photo of a white brick wall and concrete floor with a black arc floor lamp lighting the wall"></div>

  <div class="contact">
    <div class="contact__phone">
      <svg width="13" height="13" viewBox="0 0 24 24" aria-hidden="true"><circle cx="12" cy="12" r="10.5" fill="none" stroke="#1e1e1e" stroke-width="2"/><path d="M8 6.5c-1 1-1 3 1 6s4.5 5 6 5l1.5-1.5-2.5-2-1.2.8c-1-.5-2.3-2-2.8-3l.8-1.2-2-2.5z" fill="#1e1e1e"/></svg>
      518-732-5164
    </div>
    <div class="contact__email">
      <svg width="11" height="8" viewBox="0 0 11 8" aria-hidden="true"><rect width="11" height="8" fill="#3a3a3a"/><path d="M0 0l5.5 4.5L11 0" fill="none" stroke="#dcdcdc"/></svg>
      marek@veritylane-studio.net
    </div>
  </div>

  <div class="wordmark"><span>Verity Lane</span><span>Studio</span></div>

  <nav class="site-nav">
    <span class="site-nav__tab">About</span><span class="site-nav__tab">Services</span><span class="site-nav__tab">Work</span><span class="site-nav__tab">Experience</span><span class="site-nav__tab">Partners</span><span class="site-nav__tab">Contact</span>
  </nav>

  <h1 class="headline">Let’s talk<br>about taking<br>research out of<br>the dark ages.</h1>
  <p class="invite">Visit our newly launched website to learn how and get in touch</p>

  <div class="url-band">
    <svg class="url-band__icon" width="20" height="15" viewBox="0 0 20 15" aria-hidden="true"><polyline points="2,13 7,6 12,10 18,2" fill="none" stroke="#fff" stroke-width="2.2"/></svg>
    www.veritylane-studio.net
    <div class="social"><span class="social__dot"></span><span class="social__dot"></span><span class="social__dot"></span></div>
  </div>
</section>

<section class="postcard postcard--back" aria-label="Back side">
  <div class="scene-wall" role="img" aria-label="Light blue painted brick wall texture"></div>

  <div class="contact">
    <div class="contact__phone">
      <svg width="13" height="13" viewBox="0 0 24 24" aria-hidden="true"><circle cx="12" cy="12" r="10.5" fill="none" stroke="#1e1e1e" stroke-width="2"/><path d="M8 6.5c-1 1-1 3 1 6s4.5 5 6 5l1.5-1.5-2.5-2-1.2.8c-1-.5-2.3-2-2.8-3l.8-1.2-2-2.5z" fill="#1e1e1e"/></svg>
      518-732-5164
    </div>
    <div class="contact__email">
      <svg width="11" height="8" viewBox="0 0 11 8" aria-hidden="true"><rect width="11" height="8" fill="#3a3a3a"/><path d="M0 0l5.5 4.5L11 0" fill="none" stroke="#aad"/></svg>
      marek@veritylane-studio.net
    </div>
  </div>

  <p class="tagline">Consumer insights<br>that get noticed.</p>
  <div class="wordmark"><span>Verity Lane</span><span>Studio</span></div>
  <p class="strapline">A leading edge marketing<br>partnership that really works.</p>

  <nav class="site-nav">
    <span class="site-nav__tab site-nav__tab--active">About</span><span class="site-nav__tab">Services</span><span class="site-nav__tab">Work</span><span class="site-nav__tab">Experience</span><span class="site-nav__tab">Partners</span><span class="site-nav__tab">Contact</span>
  </nav>

  <div class="feature" style="left:29px">
    <div class="feature__card">Great Design
      <svg class="feature__mark" viewBox="0 0 38 38" role="img" aria-label="Colourful linked hexagon design icon"><rect x="4" y="4" width="30" height="30" rx="6" fill="#3f8ad4"/></svg>
    </div>
    <div class="feature__cta">Find out more</div>
  </div>

  <div class="feature" style="left:210px">
    <div class="feature__card">Expert Partners
      <svg class="feature__mark" viewBox="0 0 38 38" role="img" aria-label="Group of partners icon"><rect x="4" y="4" width="30" height="30" rx="6" fill="#f2a33a"/></svg>
    </div>
    <div class="feature__cta feature__cta--grey">See how we can help</div>
  </div>

  <div class="feature" style="left:391px">
    <div class="feature__card">Award-winning Insights
      <svg class="feature__mark" viewBox="0 0 38 38" role="img" aria-label="Award badge"><circle cx="19" cy="19" r="15" fill="#cfb054"/></svg>
    </div>
    <div class="feature__cta">Check out our work</div>
  </div>

  <div class="help-panel">
    <h2 class="help-panel__title">How we can help...</h2>
    <p>Think of us as your go-to resource for identifying and incorporating the most innovative and exciting techniques into your research programs. We carefully curate and develop close partnerships with the best of the best - from online qualitative research and mobile ethnography to social media listening and fresh takes on concept testing, we can guide the way.</p>
    <p>Plus, we believe that socializing consumer learning is just as critical as gathering it. By taking insights deliverables to the next level – through infographics, videos, magazines, interactive profiles and so much more – we are getting stakeholders excited to engage with research and inspired to take action because of it. It’s a new way to look at insights from a new type of partner. And, it’s a new way to get the most from your research dollars.</p>
  </div>

  <div class="url-band">
    <svg class="url-band__icon" width="20" height="15" viewBox="0 0 20 15" aria-hidden="true"><polyline points="2,13 7,6 12,10 18,2" fill="none" stroke="#fff" stroke-width="2.2"/></svg>
    www.veritylane-studio.net
    <div class="social"><span class="social__dot"></span><span class="social__dot"></span><span class="social__dot"></span></div>
  </div>
</section>

</body>
</html>
```